Sci Fi/ Secret Agent Author needs website design!

My name is Lark Whitby and I am an author. I require a site that can provide information about myself and my books and other works.

I would like it to have a Home, blog function, (about the) books/series section so people can visit another section and read about each individual book that's going to be released. A resources page, a Store, social media links and ability to load/embed videos from clipvane and other.

I write mild scifi/thriller/conspiracy/secret government type novels. -At the moment-. The series follows a strong female lead that is an agent with a secret organisation in a classified military installation.

The theme would be professional yet possibly show this element.

/military fiction/thriller/fantasy/Sci fi/ femme-fatal, readers. Mostly females, age 18-60
Novel readers

5+ page

• Would like designers to follow brief. :)
• My budget includes all the pages I will need;
• eg home, blog, resources, store, ability to pay with coinpouch and Credit Cards
• , ability to have trailers from clipvane etc. Must have links to the social media mentioned in the brief.
• use of the colours I have suggested. electric/indigo purple, fuschia highlights , dark greys
• as I will possibly base branding for social media ETC on the look of your website design and colour scheme.
• Ability for trailer on front page??
• Should not be too cluttered. (But I am open to all ideas)

```html
<!DOCTYPE html>
<html lang="en">
<head>
<meta charset="utf-8">
<title>Lark Whitby — Author</title>
<link href="https://fonts.googleapis.com/css2?family=Jost:wght@400;500&family=Open+Sans:ital,wght@0,400;0,600;1,400&family=Great+Vibes&display=swap" rel="stylesheet">
<style>
  :root{
    --indigo:#5a0fb4;
    --ink:#222222;
    --muted:#555555;
    --soft:#f3f3f3;
    --night:#16141f;
    --line:#d6d6d6;
    --white:#ffffff;
  }
  *{margin:0;padding:0;box-sizing:border-box}
  html,body{width:713px;height:1200px;overflow:hidden;background:var(--white)}
  body{position:relative;font-family:'Open Sans',sans-serif;color:var(--ink)}
  h1,h2{font-weight:400}
  .abs{position:absolute}

  /* header */
  .site-header{position:absolute;left:0;top:0;width:713px;height:54px;background:var(--white);box-shadow:0 1px 4px rgba(0,0,0,.18);z-index:2}
  .brand{left:58px;top:16px;font-family:'Jost',sans-serif;font-size:17px;letter-spacing:.3px;color:var(--ink)}
  .main-nav a{position:absolute;top:19px;font-family:'Jost',sans-serif;font-size:10px;color:#555;text-decoration:none}
  .main-nav a.active{color:var(--indigo);font-weight:500}
  .social-top{left:512px;top:22px;width:108px;display:flex;justify-content:space-between;align-items:center;font-family:'Jost',sans-serif;font-size:6px;line-height:9px;color:#666;white-space:nowrap}
  .cart{left:630px;top:15px;width:24px;height:24px;border-radius:50%;background:var(--indigo)}

  /* hero */
  .hero{left:0;top:54px;width:713px;height:258px;background:linear-gradient(90deg,#2a2b38 0%,#4d5565 35%,#8a93a0 52%,#3a3f52 75%,#1c1c2b 100%)}
  .hero-quote{left:58px;top:74px;width:310px;font-size:10px;line-height:18.5px;color:var(--white);font-weight:600}
  .hero-meta{left:58px;top:164px;font-size:9.5px;font-style:italic;color:var(--white);display:flex;gap:8px;align-items:center}
  .dots{left:333px;top:219px;display:flex;gap:5px}
  .dots span{width:8px;height:8px;border-radius:50%;border:1.2px solid var(--white)}
  .dots span.on{background:var(--white)}
  .book-cover{left:494px;top:12px;width:128px;height:222px;background:linear-gradient(160deg,#3b4a3f,#1f6f73 40%,#2a2a2a);box-shadow:4px 4px 10px rgba(0,0,0,.5);border-right:5px solid #e9e3c8}

  /* about */
  .portrait{left:58px;top:352px;width:220px;height:236px;border:3px solid var(--white);box-shadow:0 0 0 1px var(--line),0 1px 4px rgba(0,0,0,.15);background:linear-gradient(180deg,#8b7a6a,#4a3f38 60%,#2a2a30)}
  .about-title{left:313px;top:349px;font-family:'Jost',sans-serif;font-size:17px;color:var(--ink)}
  .about-text{left:314px;width:342px;font-size:7.2px;line-height:16.3px;color:var(--muted)}
  .signature{left:338px;top:548px;font-family:'Great Vibes',cursive;font-size:22px;color:var(--indigo)}

  /* video */
  .video-band{left:0;top:633px;width:713px;height:342px;background:var(--soft)}
  .section-title{width:713px;left:0;text-align:center;font-family:'Jost',sans-serif;font-size:17px;color:var(--ink)}
  .video-frame{left:154px;top:704px;width:405px;height:232px;border:2px solid var(--white);box-shadow:0 0 0 1px var(--line);background:linear-gradient(180deg,#5e8e8c 0%,#8fb3b0 40%,#c6a2a0 55%,#3e5660 70%,#1e2430 100%)}

  /* newsletter */
  .news-sub{left:0;width:713px;text-align:center;top:1043px;font-size:9px;color:var(--muted)}
  .email-field{left:180px;top:1077px;width:269px;height:31px;border:1px solid var(--line);font-size:8px;color:#666;padding:10px 12px}
  .signup{left:449px;top:1077px;width:83px;height:31px;background:var(--indigo);color:var(--white);font-size:9.5px;font-weight:600;text-align:center;line-height:31px}

  /* footer */
  .site-footer{left:0;top:1156px;width:713px;height:44px;background:var(--night)}
  .copyright{left:58px;top:17px;font-size:7.5px;color:var(--white)}
  .social-foot{left:450px;top:15px;display:flex;gap:9px;font-size:7.5px;color:var(--white);align-items:center}
  .social-foot span::before{content:"";display:inline-block;width:6px;height:6px;border-radius:50%;border:1px solid currentColor;margin-right:3px;vertical-align:middle}
</style>
</head>
<body>

<header class="site-header">
  <div class="abs brand">LARK WHITBY</div>
  <nav class="main-nav">
    <a class="active" style="left:187px">Home</a>
    <a style="left:230px">About the book</a>
    <a style="left:314px">Resources</a>
    <a style="left:373px">Store</a>
    <a style="left:411px">Blog</a>
    <a style="left:446px">Contact us</a>
  </nav>
  <div class="abs social-top">
    <svg width="8" height="8" viewBox="0 0 10 10"><circle cx="4" cy="4" r="3" fill="none" stroke="#666" stroke-width="1.4"/><line x1="6.2" y1="6.2" x2="9" y2="9" stroke="#666" stroke-width="1.4"/></svg>
    <span>Wall</span><span>Chirp</span><span>Lens</span><span>Tack</span><span>Clipvane</span>
  </div>
  <div class="abs cart">
    <svg width="24" height="24" viewBox="0 0 24 24"><path d="M7 8h1.5l1.5 6h6l1.3-4.5H9.2" fill="none" stroke="#fff" stroke-width="1.4"/><circle cx="10.5" cy="16" r="1" fill="#fff"/><circle cx="15" cy="16" r="1" fill="#fff"/></svg>
  </div>
</header>

<section class="abs hero" role="img" aria-label="Misty street scene with a lone woman in a long coat">
  <p class="abs hero-quote">“ At vero eos et accusamus et iusto odio dignissimos duciusr qui blanditiis praesentium voluptatum deleniti atquecorru pti quos dolores et quas molestias excepturi sint occaecati cupiditatnon provident, similique sunt in culpa qui. ”</p>
  <div class="abs hero-meta">
    <svg width="9" height="9" viewBox="0 0 10 10"><rect x="1" y="2" width="8" height="7" fill="none" stroke="#fff"/><line x1="1" y1="4" x2="9" y2="4" stroke="#fff"/></svg>
    <span>20/05/2017</span><span>|</span>
    <svg width="8" height="9" viewBox="0 0 8 9"><circle cx="4" cy="2.5" r="2" fill="#fff"/><path d="M0 9c0-3 1.5-4 4-4s4 1 4 4z" fill="#fff"/></svg>
    <span>Mara Quill</span>
  </div>
  <div class="abs dots"><span class="on"></span><span></span><span></span><span></span></div>
  <div class="abs book-cover" role="img" aria-label="Book cover with a woman playing violin in a doorway"></div>
</section>

<section class="about">
  <div class="abs portrait" role="img" aria-label="Portrait photo of the author"></div>
  <h1 class="abs about-title">LARK WHITBY</h1>
  <p class="abs about-text" style="top:384px">Sed ut perspiciatis unde omnis iste natus error sit voluptatem accusantium dolorem laudantium, totam rem aperiam, eaque ipsa quae ab illo inventore veritatis et quasi architecto beatae vitdict a sunt explica am voluptatem quia voluptas.</p>
  <p class="abs about-text" style="top:449px">Aspernatur aut odit aut fugit, sed quia consequuntur magni dolores eos qui ratione voluptatemse qui nesciunt. Neque porro quisquam est, qui dolorem ipsum quia dolor sit amet, consectetur, adi pisci velit, sed quia non numquam eius modi tempora incidunt ut labore et dolore magnam uam quaerat voluptatem. Ut enim ad minima veniam, quis nostrum exercitationem ullam corporissus cipit laboriosam, nisi ut aliquid ex ea commodi conseql.</p>
  <svg class="abs" style="left:286px;top:540px" width="40" height="34" viewBox="0 0 40 34"><path d="M2 3 C8 18 20 27 36 28" fill="none" stroke="#777" stroke-width="1"/><path d="M28 23 L36 28 L28 32" fill="none" stroke="#777" stroke-width="1"/></svg>
  <div class="abs signature">Lark Whitby</div>
</section>

<section class="abs video-band">
  <h2 class="abs section-title" style="top:32px">WATCH OUR VIDEO</h2>
</section>
<div class="abs video-frame" role="img" aria-label="Video still: silhouette of a man holding a lantern by the sea at dusk">
  <svg class="abs" style="left:181px;top:94px" width="40" height="40" viewBox="0 0 40 40"><circle cx="20" cy="20" r="19" fill="#111"/><path d="M15 12 L28 20 L15 28 Z" fill="#fff"/></svg>
</div>

<section class="newsletter">
  <h2 class="abs section-title" style="top:1011px">NEWSLETTER SIGN UP</h2>
  <p class="abs news-sub">Register your Email Address to get information about us</p>
  <div class="abs email-field">Email Address</div>
  <div class="abs signup">SIGN UP</div>
</section>

<footer class="abs site-footer">
  <p class="abs copyright">Copyright © 2017, Lark Whitby. All rights are reserved.</p>
  <div class="abs social-foot"><span>Wall</span><span>Chirp</span><span>Tack</span><span>Lens</span><span>Clipvane</span></div>
</footer>

</body>
</html>
```